Property management company looking for modern card design

We at Blue Heron Partners provides property management services for its residential and commercial properties, with expertise in all categories of multifamily, industrial and office projects throughout California.

We need a business card design that is professional and modern designed business card. In our field, clients get hundreds of business cards, we would like our card to stand out.

Please avoid small print.

Target Market(s)

Professionals and high end clients

Industry/Entity Type

Financial Planning

Contact Information for Business Card

Company Name: Blue Heron Partners, Name, email, license #, phone number, website blueheronpartners.com

Font styles to use
Sans Serif

Requirements
Must have
• The card design needs to be adaptable because there is a possibly we will be expanding into different sectors other than real estate. The card design should be focused on financial planning and asset management.
Nice to have
• Modern and simple business card. Eye catching. Non-standard size/shaped cards would be great.
• blueheronpartners.com
Should not have
• Too many bright color or any pictures or shapes of real estate stuff.

```html
<!DOCTYPE html>
<html lang="en">
<head>
<meta charset="utf-8">
<title>Blue Heron Partners – Business Card</title>
<link rel="stylesheet" href="https://fonts.googleapis.com/css2?family=Anton&family=Arimo:wght@700&family=Questrial&display=swap">
<style>
  :root {
    --backdrop-light: #ecebd9;
    --backdrop-mid: #cfc9ae;
    --backdrop-dark: #a9a38a;
    --kraft: #9c7526;
    --kraft-light: #a57d2c;
    --kraft-dark: #8f6a20;
    --band: #47414b;
    --rule: #4a4852;
    --accent-red: #b00b0b;
    --ink: #111111;
    --web-grey: #4d4a52;
  }
  * { margin: 0; padding: 0; box-sizing: border-box; }
  html, body { width: 900px; height: 1200px; overflow: hidden; }
  body {
    position: relative;
    background: radial-gradient(ellipse at 50% 52%, var(--backdrop-light) 0%, var(--backdrop-mid) 55%, var(--backdrop-dark) 100%);
    font-family: "Arimo", Arial, sans-serif;
  }
  .card {
    position: absolute;
    background:
      repeating-linear-gradient(90deg, rgba(0,0,0,0.035) 0 1px, transparent 1px 3px),
      linear-gradient(160deg, var(--kraft-light), var(--kraft) 50%, var(--kraft-dark));
    overflow: hidden;
  }
  .card--front { left: 315px; top: 142px; width: 301px; height: 527px; }
  .card--back { left: 187px; top: 722px; width: 527px; height: 302px; }

  .brand-dot {
    position: absolute;
    border-radius: 50%;
    background: var(--accent-red);
  }
  .card--front .brand-dot { left: 111px; top: 68px; width: 80px; height: 80px; }
  .card--back .brand-dot { left: 218px; top: 62px; width: 90px; height: 90px; }

  .brand-name {
    position: absolute;
    left: 0; right: 0;
    text-align: center;
    font-family: "Questrial", Arial, sans-serif;
    color: var(--accent-red);
    white-space: nowrap;
  }
  .card--front .brand-name { top: 158px; font-size: 20px; letter-spacing: 2px; }
  .card--back .brand-name { top: 178px; font-size: 25px; letter-spacing: 2.5px; }

  .rule {
    position: absolute;
    height: 3px;
    background: var(--rule);
  }
  .card--front .rule { left: 19px; width: 267px; }

  .band { position: absolute; background: var(--band); }
  .name-band { left: 41px; top: 231px; width: 260px; height: 53px; }
  .person-name {
    position: absolute;
    right: 27px; top: 238px;
    font-family: "Anton", Impact, sans-serif;
    font-size: 31px;
    font-weight: 400;
    line-height: 40px;
    color: var(--ink);
  }

  .contact {
    position: absolute;
    right: 21px; top: 386px;
    text-align: right;
    font-size: 13px;
    font-weight: 700;
    line-height: 25px;
    color: var(--ink);
    list-style: none;
    white-space: nowrap;
  }

  .website {
    position: absolute;
    left: 0; right: 0;
    text-align: center;
    font-weight: 700;
    color: var(--web-grey);
    font-size: 18px;
  }
  .card--front .website { top: 489px; }
  .card--back .website { top: 261px; }

  .side-band { top: 119px; width: 76px; height: 52px; }
  .side-band--left { left: 0; }
  .side-band--right { right: 0; }
</style>
</head>
<body>

<section class="card card--front" aria-label="Business card front">
  <div class="brand-dot"></div>
  <div class="brand-name">Blue Heron Partners</div>

  <div class="rule" style="top:224px"></div>
  <div class="band name-band"></div>
  <h1 class="person-name">Daniel Reyes</h1>
  <div class="rule" style="top:289px"></div>

  <div class="rule" style="top:370px"></div>
  <ul class="contact">
    <li>daniel.reyes@blueheronpartners.com</li>
    <li>License Nr:004812</li>
    <li>Phone 555-201-4870</li>
  </ul>
  <div class="rule" style="top:475px"></div>

  <div class="website">blueheronpartners.com</div>
</section>

<section class="card card--back" aria-label="Business card back">
  <div class="band side-band side-band--left"></div>
  <div class="band side-band side-band--right"></div>
  <div class="brand-dot"></div>
  <div class="brand-name">Blue Heron Partners</div>
  <div class="rule" style="top:248px; left:36px; width:456px;"></div>
  <div class="website">blueheronpartners.com</div>
</section>

</body>
</html>
```